Card design for orthopaedic surgeons working as The Brightwater Joint Centre

Business cards, letterhead

Colors

Designer to choose colors to be used in the design.

Requirements
Must have
• Late addition.
• Cards letterhead must have logos of
• Crestmoor Lindell College of Surgeons
• Varenwood Bone Health Association
Nice to have
• Back of card to have space for appointment time to be added by hand and some blank space for writing incidental other notes.

```html
<!DOCTYPE html>
<html lang="en">
<head>
<meta charset="UTF-8">
<title>The Brightwater Joint Centre – Business Cards</title>
<link href="https://fonts.googleapis.com/css2?family=Lato:wght@300;400;700;900&display=swap" rel="stylesheet">
<style>
  :root {
    --backdrop: #2c3034;
    --navy: #0b3350;
    --sky: #4fa3dc;
    --paper: #ffffff;
  }
  * { margin: 0; padding: 0; box-sizing: border-box; }
  html, body { width: 1200px; height: 900px; overflow: hidden; }
  body {
    background: var(--backdrop);
    font-family: "Lato", sans-serif;
    position: relative;
  }
  .card {
    position: absolute;
    left: 250px;
    width: 700px;
    height: 400px;
    overflow: hidden;
    border-radius: 4px;
    box-shadow: 0 10px 30px rgba(0,0,0,0.35);
  }
  .card--front { top: 470px; background: var(--paper); }
  .card--back { top: 40px; background: var(--navy); }

  .card__shapes { position: absolute; inset: 0; }

  .brand-name {
    position: absolute;
    font-weight: 300;
    white-space: nowrap;
    letter-spacing: -0.5px;
  }
  .card--front .brand-name {
    left: 90px; top: 60px;
    font-size: 28px;
    color: var(--navy);
  }
  .card--back .brand-name {
    left: 0; right: 0; top: 170px;
    text-align: center;
    font-size: 44px;
    color: var(--sky);
  }

  .person {
    position: absolute;
    right: 44px; top: 150px;
    text-align: right;
  }
  .person__name {
    font-weight: 900;
    font-size: 34px;
    line-height: 40px;
    color: var(--navy);
    letter-spacing: 1px;
    text-transform: uppercase;
  }
  .person__role {
    font-size: 20px;
    line-height: 26px;
    color: var(--sky);
    margin-top: 2px;
  }

  .contact {
    position: absolute;
    left: 200px; width: 270px; top: 306px;
    list-style: none;
  }
  .contact__item {
    display: flex;
    justify-content: flex-end;
    align-items: center;
    gap: 10px;
    height: 28px;
    font-size: 17px;
    color: var(--sky);
    white-space: nowrap;
  }
  .contact__icon { width: 18px; height: 18px; flex: none; }
</style>
</head>
<body>

  <section class="card card--back" aria-label="Business card back">
    <p class="brand-name">The Brightwater Joint Centre</p>
  </section>

  <section class="card card--front" aria-label="Business card front">
    <svg class="card__shapes" viewBox="0 0 700 400" width="700" height="400" aria-hidden="true">
      <path class="wave wave--outer" d="M0,96 C20,200 160,226 300,244 C420,258 500,280 540,322 C570,355 590,385 600,400 L0,400 Z" fill="var(--sky)"/>
      <path class="wave wave--gap" d="M0,112 C20,214 160,238 300,252 C420,264 500,284 540,326 C570,357 590,386 600,400 L0,400 Z" fill="var(--paper)"/>
      <path class="wave wave--inner" d="M0,120 C20,222 160,244 300,257 C420,267 500,287 540,328 C570,358 590,386 600,400 L0,400 Z" fill="var(--sky)"/>
      <path class="wave wave--base" d="M0,130 C20,230 160,250 300,262 C420,272 500,290 540,330 C570,360 590,385 600,400 L0,400 Z" fill="var(--navy)"/>
    </svg>

    <p class="brand-name">The Brightwater Joint Centre</p>

    <div class="person">
      <p class="person__name">Daniel Hartley</p>
      <p class="person__role">Founder &amp; CEO</p>
    </div>

    <ul class="contact">
      <li class="contact__item">1234567890
        <svg class="contact__icon" viewBox="0 0 24 24" aria-hidden="true"><path d="M6.6 10.8a15 15 0 0 0 6.6 6.6l2.2-2.2a1 1 0 0 1 1-.25 11.4 11.4 0 0 0 3.6.57 1 1 0 0 1 1 1V20a1 1 0 0 1-1 1A17 17 0 0 1 3 4a1 1 0 0 1 1-1h3.5a1 1 0 0 1 1 1c0 1.25.2 2.45.57 3.6a1 1 0 0 1-.25 1z" fill="#fff"/></svg>
      </li>
      <li class="contact__item">info@yourmail.com
        <svg class="contact__icon" viewBox="0 0 24 24" aria-hidden="true"><rect x="2" y="5" width="20" height="14" rx="1" fill="#fff"/><path d="M2.5 5.5 12 13l9.5-7.5" fill="none" stroke="var(--navy)" stroke-width="1.6"/></svg>
      </li>
      <li class="contact__item">www.yourwebsite.com
        <svg class="contact__icon" viewBox="0 0 24 24" aria-hidden="true"><circle cx="12" cy="12" r="10" fill="#fff"/><g fill="none" stroke="var(--navy)" stroke-width="1.3"><ellipse cx="12" cy="12" rx="4.5" ry="10"/><path d="M2 12h20M4 7h16M4 17h16"/></g></svg>
      </li>
    </ul>
  </section>

</body>
</html>
```